International Clinical Software Company needs a new business card design

We are looking for a new business card design for our company that has recently expanded into the UK market, making us a multinational company.
After having rebranded our website and produced a new style guide, we are looking for a business card that is creative and attention grabbing, while being consistent with the style and colour scheme used on the new website, www.plumvora.example
We produce care management technology for the aged care market, but the main aspect we aim to communicate is the human element of our software, and the way it assists in providing better care for aged people, and stronger relationships between aged people and the staff that care for them.
Our current business card is a dark green with gold text, which makes the text quite difficult to read, not very aesthetically appealing and the colour scheme looks quite dated.
We would like something fresh and modern, that can still be colourful but doesn't use large blocks of dark colour, and uses the colours within our logo.
Something tying in with the leaves that are used in our logo could work quite nicely, along with the Autumn/Fall colours of soft greens, yellows and reds (also in our existing logo). However also happy to look at fresh, completely out of the box ideas we may not have yet considered.
Target Market(s)
The people that receive this business card work in the aged card or health industry and are either corporate/management level staff or clinical (Registered Nurses, care workers etc.)
Industry/Entity Type
Health Product
Contact Information for Business Card
Company Name - BrindlewayCare
Company locations: United Kingdom, Australia, New Zealand
Staff Details:
Staff name: Derek Mallow
Staff job title: Executive Chairman
Staff email: d.mallow@plumvora.example
Office phone number: 01742 918576
Font styles to use
Other font styles liked:
- Calibri
Requirements
Must have
- Must include the BrindlewayCare brand name in it's current font
- Must include logo (3 leaves in gold circle)
- Must include Business Card Details
Nice to have
- Elements of gold
- White space
- Something autumn themed but not too cliched
Should not have
- No blue - used by a major competitor and we would like to differentiate from them
- Large blocks of dark green colour (the green that appears in our leaves on the logo on our current business card is the background colour and it is far too dark)

```html
<!DOCTYPE html>
<html lang="en">
<head>
<meta charset="utf-8">
<title>BrindlewayCare Business Card</title>
<link rel="stylesheet" href="https://fonts.googleapis.com/css2?family=Open+Sans:wght@300;400;600&display=swap">
<style>
  :root {
    --gold: #ae9a6b;
    --gold-text: #9c8b5c;
    --white: #ffffff;
    --faint: #efece4;
    --backdrop: #ecebe8;
  }
  * { margin: 0; padding: 0; box-sizing: border-box; }
  html, body {
    width: 1200px;
    height: 900px;
    overflow: hidden;
    background: var(--backdrop);
    font-family: "Open Sans", "Calibri", sans-serif;
  }
  .card {
    position: absolute;
    background: var(--white);
    overflow: hidden;
    box-shadow: 0 4px 18px rgba(0, 0, 0, 0.12);
  }

  /* Front */
  .card-front { left: 77px; top: 34px; width: 589px; height: 364px; }
  .brand {
    position: absolute;
    left: 34px;
    top: 52px;
    display: flex;
    align-items: center;
    gap: 22px;
  }
  .brand-mark {
    width: 104px;
    height: 104px;
    border-radius: 50%;
    border: 3px solid var(--gold);
  }
  .brand-name {
    font-weight: 300;
    font-size: 40px;
    color: var(--gold-text);
    letter-spacing: 0.5px;
  }
  .details-band {
    position: absolute;
    left: 0;
    top: 165px;
    width: 100%;
    height: 199px;
    background: var(--gold);
    color: var(--white);
    padding: 22px 31px 0;
  }
  .staff-name { font-weight: 600; font-size: 21px; line-height: 1.2; }
  .staff-title { font-size: 15.5px; line-height: 1.3; }
  .locations { margin-top: 20px; font-size: 15.5px; line-height: 1.4; }
  .contact {
    margin-top: 20px;
    display: flex;
    align-items: center;
    gap: 7px;
    font-size: 15.5px;
  }
  .contact svg { width: 13px; height: 13px; }

  /* Back */
  .card-back { left: 388px; top: 505px; width: 567px; height: 352px; }
  .back-ring {
    position: absolute;
    left: 92px;
    top: -15px;
    width: 380px;
    height: 380px;
    border-radius: 50%;
    border: 8px solid var(--faint);
  }
  .name-band {
    position: absolute;
    left: 0;
    top: 110px;
    width: 100%;
    height: 131px;
    background: var(--gold);
    display: flex;
    align-items: center;
    justify-content: center;
  }
  .name-band .brand-name {
    color: var(--white);
    font-size: 58px;
  }
</style>
</head>
<body>
  <section class="card card-front">
    <div class="brand">
      <div class="brand-mark"></div>
      <span class="brand-name">BrindlewayCare</span>
    </div>
    <div class="details-band">
      <p class="staff-name">Derek Mallow</p>
      <p class="staff-title">Executive Chairman</p>
      <p class="locations">United Kingdom, Australia<br>New Zealand</p>
      <p class="contact">
        <svg viewBox="0 0 24 24" aria-hidden="true"><path fill="#fff" d="M6.6 10.8a15.1 15.1 0 0 0 6.6 6.6l2.2-2.2c.3-.3.7-.4 1-.2 1.1.4 2.3.6 3.6.6.6 0 1 .4 1 1V20c0 .6-.4 1-1 1A17 17 0 0 1 3 4c0-.6.4-1 1-1h3.5c.6 0 1 .4 1 1 0 1.3.2 2.5.6 3.6.1.3 0 .7-.2 1z"/></svg>
        d.mallow@plumvora.example
      </p>
    </div>
  </section>

  <section class="card card-back">
    <div class="back-ring"></div>
    <div class="name-band">
      <span class="brand-name">BrindlewayCare</span>
    </div>
  </section>
</body>
</html>
```